American cannabis tech company business card design

Pavrel.com is seeking a modern, professional, and brand-aligned business card that represents our company and its core values: Mission, Story, Values, and Impact. As an innovative cannabis company, we want a business card that is not only visually appealing but also serves as a representation of who we are and what we stand for.

Project Scope: Design a double-sided business card that integrates our brand identity and core values. Incorporate our key brand elements, ensuring a sleek and contemporary aesthetic. Visually reflect our core values (Mission, Story, Values, Impact) in a way that is engaging yet professional.

Target Market(s)

Vendors, third parties,

Contact Information for Business Card

Contact details (name, title, email, phone, website, etc.)

Font styles to use
Other font styles liked:
• Caslon, Centra

Colors

Designer to choose colors to be used in the design.

Requirements
Must have
• Pavrel.com logo and branding A creative yet clean way to integrate our core values (Mission, Story, Values, Impact) Modern typography and a well-structured layout
Nice to have
• forest green, grey, white, black
Should not have
• references to marijuana, leafs, plants, or related product

```html
<!DOCTYPE html>
<html lang="en">
<head>
<meta charset="utf-8">
<title>Pavrel.com Business Card</title>
<link rel="stylesheet" href="https://fonts.googleapis.com/css2?family=Montserrat:wght@400;500;700;800&display=swap">
<style>
  :root {
    --forest: #1a3320;
    --white: #ffffff;
    --paper: #f7f7f5;
    --ink: #1b1b1b;
    --stage: #e4e5e3;
  }
  * { margin: 0; padding: 0; box-sizing: border-box; }
  html, body { width: 1200px; height: 900px; overflow: hidden; }
  body {
    background: var(--stage);
    font-family: "Montserrat", Arial, sans-serif;
    position: relative;
  }
  .card {
    position: absolute;
    left: 300px;
    width: 600px;
    height: 343px;
    border-radius: 22px;
    overflow: hidden;
    box-shadow: 0 6px 18px rgba(0,0,0,0.18);
  }
  .card-front { top: 80px; background: var(--forest); }
  .card-back  { top: 477px; background: var(--paper); }

  .wordmark {
    position: absolute;
    left: 0; right: 0;
    text-align: center;
    font-weight: 800;
    letter-spacing: 2px;
    line-height: 1;
  }
  .card-front .wordmark { top: 125px; font-size: 92px; color: var(--white); }
  .card-back .wordmark  { top: 58px;  font-size: 72px; color: var(--forest); }

  .contact-band {
    position: absolute;
    left: 0; right: 0;
    top: 178px;
    height: 90px;
    background: var(--forest);
    color: var(--white);
  }
  .person {
    position: absolute;
    right: 340px;
    top: 20px;
    text-align: right;
  }
  .person-name { font-size: 22px; font-weight: 700; }
  .person-title { font-size: 13px; font-weight: 400; margin-top: 2px; opacity: 0.9; }
  .divider {
    position: absolute;
    left: 276px;
    top: 16px;
    width: 2px;
    height: 58px;
    background: var(--white);
  }
  .contact-list {
    position: absolute;
    left: 296px;
    top: 16px;
    list-style: none;
    font-size: 14px;
    line-height: 19px;
  }
  .contact-list li { display: flex; align-items: center; gap: 10px; }
  .contact-list svg { width: 11px; height: 11px; fill: var(--white); flex: none; }
  .address {
    position: absolute;
    left: 0; right: 0;
    top: 292px;
    text-align: center;
    font-size: 14px;
    color: var(--ink);
  }
</style>
</head>
<body>
  <section class="card card-front">
    <div class="wordmark">PAVREL</div>
  </section>

  <section class="card card-back">
    <div class="wordmark">PAVREL</div>
    <div class="contact-band">
      <div class="person">
        <div class="person-name">Owen Hartley</div>
        <div class="person-title">Co-Founder &amp; CEO</div>
      </div>
      <div class="divider"></div>
      <ul class="contact-list">
        <li>
          <svg viewBox="0 0 12 12" aria-hidden="true"><path d="M2.5 1h2l1 3-1.3 1a6 6 0 0 0 2.8 2.8l1-1.3 3 1v2a1 1 0 0 1-1 1A9.5 9.5 0 0 1 1.5 2a1 1 0 0 1 1-1z"/></svg>
          +1 405-555-0148
        </li>
        <li>
          <svg viewBox="0 0 12 12" aria-hidden="true"><path d="M1 2.5h10v7H1z M1 2.5l5 4 5-4" fill="none" stroke="#fff" stroke-width="1.4"/></svg>
          team@pavrel.com
        </li>
        <li>
          <svg viewBox="0 0 12 12" aria-hidden="true"><circle cx="6" cy="6" r="5" fill="none" stroke="#fff" stroke-width="1.2"/><path d="M1 6h10M6 1c-2.5 3-2.5 7 0 10M6 1c2.5 3 2.5 7 0 10" fill="none" stroke="#fff" stroke-width="1"/></svg>
          www.pavrel.com
        </li>
      </ul>
    </div>
    <div class="address">1180 Birch Avenue Dallas, TX 75204</div>
  </section>
</body>
</html>
```